Bran-well Tide Gate Custom Brokers Limited

Name: Lorvina Hadcott
Title: Customs Broker
Address: Shop 9 Ferncliff Commercial Complex
207-209 Mulgrave Road
Kingston 8
Telephone: (876)
Email: tidegatewell@mailbrook.example

```html
<!DOCTYPE html>
<html lang="en">
<head>
<meta charset="utf-8">
<title>Bran-well Tide Gate Custom Brokers Limited – Business Card</title>
<link rel="stylesheet" href="https://fonts.googleapis.com/css2?family=Poppins:wght@400;500;600;700&display=swap">
<style>
  :root {
    --navy: #0b2b52;
    --gold: #e9a516;
    --white: #ffffff;
    --grey: #9aa3ad;
    --backdrop: #1c1c1e;
  }
  html, body {
    margin: 0;
    width: 1200px;
    height: 1189px;
    overflow: hidden;
    background: var(--backdrop);
    font-family: "Poppins", sans-serif;
  }
  .card {
    position: absolute;
    left: 160px;
    width: 880px;
    height: 503px;
    border-radius: 34px;
    box-sizing: border-box;
  }
  .card--front {
    top: 62px;
    background: var(--navy);
    display: flex;
    align-items: center;
    justify-content: center;
  }
  .card--back {
    top: 624px;
    background: var(--white);
    display: flex;
    align-items: center;
    padding: 0 60px 0 70px;
  }
  .brand {
    display: flex;
    align-items: center;
    gap: 18px;
  }
  .brand__mark {
    width: 56px;
    height: 56px;
    border-radius: 50%;
    background: var(--gold);
    flex: none;
  }
  .brand__name {
    font-weight: 600;
    font-size: 30px;
    line-height: 1.2;
    letter-spacing: 0.5px;
    text-transform: uppercase;
  }
  .card--front .brand__name { color: var(--white); }
  .card--back .brand__name { color: var(--navy); font-size: 24px; }
  .card--back .brand__mark { width: 46px; height: 46px; }
  .card--back .brand { width: 360px; }
  .divider {
    width: 2px;
    height: 250px;
    background: var(--navy);
    margin: 0 44px 0 30px;
    flex: none;
  }
  .contact__name {
    margin: 0;
    color: var(--navy);
    font-weight: 700;
    font-size: 28px;
    letter-spacing: 0.5px;
    text-transform: uppercase;
  }
  .contact__title {
    margin: 2px 0 22px 12px;
    color: var(--gold);
    font-weight: 500;
    font-size: 22px;
  }
  .contact__address {
    margin: 0 0 20px 28px;
    color: var(--navy);
    font-size: 19px;
    line-height: 1.35;
    font-style: normal;
  }
  .contact__line {
    display: flex;
    align-items: center;
    gap: 14px;
    margin: 6px 0 0 28px;
    color: var(--navy);
    font-size: 19px;
  }
  .contact__icon {
    width: 26px;
    height: 26px;
    flex: none;
  }
</style>
</head>
<body>

<section class="card card--front">
  <div class="brand">
    <span class="brand__mark"></span>
    <span class="brand__name">Bran-well Tide Gate<br>Custom Brokers Ltd.</span>
  </div>
</section>

<section class="card card--back">
  <div class="brand">
    <span class="brand__mark"></span>
    <span class="brand__name">Bran-well Tide Gate<br>Custom Brokers Ltd.</span>
  </div>

  <div class="divider"></div>

  <div class="contact">
    <h1 class="contact__name">Lorvina Hadcott</h1>
    <p class="contact__title">Customs Broker</p>
    <address class="contact__address">
      Shop 9 Ferncliff<br>
      Commercial Complex<br>
      207-209 Mulgrave Road,<br>
      Kingston 8
    </address>
    <div class="contact__line">
      <svg class="contact__icon" viewBox="0 0 26 26" aria-hidden="true">
        <circle cx="13" cy="13" r="13" fill="var(--gold)"/>
        <rect x="9" y="6.5" width="8" height="13" rx="1.5" fill="none" stroke="#fff" stroke-width="1.8"/>
      </svg>
      <span>(876) 555 014 2271</span>
    </div>
    <div class="contact__line">
      <svg class="contact__icon" viewBox="0 0 26 26" aria-hidden="true">
        <circle cx="13" cy="13" r="13" fill="var(--gold)"/>
        <rect x="6.5" y="8.5" width="13" height="9" rx="1" fill="none" stroke="#fff" stroke-width="1.6"/>
        <path d="M6.8 9 L13 14 L19.2 9" fill="none" stroke="#fff" stroke-width="1.6"/>
      </svg>
      <span>tidegatewell@mailbrook.example</span>
    </div>
  </div>
</section>

</body>
</html>
```